Business Card for Fashion House

We need a business card design for our personalize fashion service for our customers. the business card should reflect reliability, luxury and creativity.
The brand Gravetto is extracted from "Graceful Velvetto"; Gravetto provides fashion designs sprinkled with luxury and style tailored for our elite clients character profile.
Gravetto is created for those who embody class and elegance with a passion for style.
Target Market(s)
Affluent Customers
Industry/Entity Type
Fashion
Contact Information for Business Card
Samira Haddadin
Fashion Designer
Telephone: +971 4 555 0192
Mobile +971 50 555 0147
Emal info@gravetto-example.com
Website www.gravetto-example.com
Social Media Youtube g+ Facebook Instagram Pin /gravetto
Font styles to use
Other font styles liked:
- Audrey provided
Look and feel
Each slider illustrates characteristics of the customer's brand and the style your logo design should communicate.

```html
<!DOCTYPE html>
<html lang="en">
<head>
<meta charset="utf-8">
<title>Gravetto Business Card</title>
<link rel="stylesheet" href="https://fonts.googleapis.com/css2?family=Marcellus&family=Roboto:wght@400&display=swap">
<style>
  :root {
    --backdrop: #3b3b3d;
    --card: #1b1b1d;
    --silver: #b9b9bc;
    --silver-soft: #8a8a8e;
    --ink: #f2f2f2;
  }
  * { margin: 0; padding: 0; box-sizing: border-box; }
  html, body { width: 799px; height: 1200px; overflow: hidden; }
  body {
    background: var(--backdrop);
    display: flex; flex-direction: column; justify-content: space-around; align-items: center;
    padding: 60px 0;
  }
  .card {
    position: relative;
    width: 680px; height: 389px;
    background: var(--card);
    border-radius: 3px;
    box-shadow: 0 12px 30px rgba(0,0,0,.45);
  }
  .brand {
    position: absolute;
    display: flex; flex-direction: column; align-items: center;
    color: var(--silver);
    font-family: "Marcellus", serif;
  }
  .brand-mark {
    width: 64px; height: 64px; border-radius: 50%;
    border: 3px solid var(--silver);
    margin-bottom: 18px;
  }
  .brand-name { font-size: 34px; letter-spacing: 14px; padding-left: 14px; line-height: 1; }
  .card-front .brand { left: 0; right: 0; top: 120px; }

  .card-back .brand { right: 56px; top: 36px; }
  .card-back .brand-mark { width: 56px; height: 56px; margin-bottom: 14px; }
  .card-back .brand-name { font-size: 26px; letter-spacing: 10px; padding-left: 10px; }

  .holder { position: absolute; left: 40px; top: 106px; color: var(--ink); }
  .holder-name { font-family: "Marcellus", serif; font-size: 24px; line-height: 1.2; }
  .holder-role { font-family: "Roboto", sans-serif; font-size: 12px; margin-top: 2px; }

  .divider {
    position: absolute; left: 240px; right: 40px; top: 152px; height: 1px;
    background: linear-gradient(90deg, var(--ink), var(--silver-soft));
  }

  .contacts {
    position: absolute; left: 40px; top: 182px;
    list-style: none;
    font-family: "Roboto", sans-serif; font-size: 15px; color: var(--ink);
  }
  .contacts li { display: flex; align-items: center; gap: 12px; height: 26px; }
  .contacts svg { width: 15px; height: 15px; fill: none; stroke: var(--ink); stroke-width: 1.6; }

  .social {
    position: absolute; right: 48px; bottom: 40px;
    display: flex; align-items: center; gap: 8px;
    font-family: "Roboto", sans-serif; font-size: 18px; color: var(--ink);
  }
  .social-dot { width: 12px; height: 12px; border-radius: 50%; background: var(--silver); }
</style>
</head>
<body>
  <section class="card card-front">
    <div class="brand">
      <span class="brand-mark"></span>
      <span class="brand-name">GRAVETTO</span>
    </div>
  </section>

  <section class="card card-back">
    <div class="brand">
      <span class="brand-mark"></span>
      <span class="brand-name">GRAVETTO</span>
    </div>
    <div class="holder">
      <p class="holder-name">Samira Haddadin</p>
      <p class="holder-role">Fashion Designer</p>
    </div>
    <div class="divider"></div>
    <ul class="contacts">
      <li><svg viewBox="0 0 16 16"><path d="M4 2l2.5 3-1.5 1.5a8 8 0 0 0 4.5 4.5L11 9.5l3 2.5-1.5 2.5C7 14 2 9 1.5 3.5z"/></svg>+971 4 555 0192</li>
      <li><svg viewBox="0 0 16 16"><rect x="4" y="1.5" width="8" height="13" rx="1.5"/><line x1="7" y1="12" x2="9" y2="12"/></svg>+971 50 555 0147</li>
      <li><svg viewBox="0 0 16 16"><rect x="1.5" y="3.5" width="13" height="9"/><path d="M1.5 3.5L8 9l6.5-5.5"/></svg>info@gravetto-example.com</li>
      <li><svg viewBox="0 0 16 16"><circle cx="8" cy="8" r="6.5"/><ellipse cx="8" cy="8" rx="2.8" ry="6.5"/><line x1="1.5" y1="8" x2="14.5" y2="8"/></svg>www.gravetto-example.com</li>
    </ul>
    <div class="social">
      <span class="social-dot"></span>
      <span>/gravetto</span>
    </div>
  </section>
</body>
</html>
```